Business Card (double-sided) and Stationary Design for dental office

1) Business Card Design: We need a business card design for a dental specialty office.
Texts should contain:
The name of our office "Brindle Oaks Orthodontics"
Tagline: "Specialist in Orthodontic and Maxillofacial Orthopedics"
Tag line: "Creating "Tolvering" smiles for Children and Adults"
Doctor name: "Doctor Name"
Office Address:
"123 Street Name
City, State Zip code"
Office email address: office@brindleoaksortho.com
Website: www.brindleoaksortho.com

We will provide the full office address once the design is selected
Theme: beach, paradise, coastal, wave
We would like to have some creativity in design. Some acceptable ideas: front page: logo and office name. Back page: more detail information, and map to office in form of an island. Please see sample from our other location, but you DON'T HAVE TO USE OR COPY THE SAME CONCEPT.

IF POSSIBLE, PLEASE SUBMIT AT LEAST TWO CONCEPTS: ONE WITH THE BACK LOOKING SIMILAR TO WHAT IS IN THE SAMPLE, AND ONE DIFFERENT.

Color: designer to choose. We have different shade of blues and sand color in our office. Please see logo.

2) Please also design a matching set of stationary that compliment the business card and our logo.

Target Market(s)

Dental

Contact Information for Business Card

See descriptions

Font styles to use
Other font styles liked:
• Matching texts in logo

Colors
0054AA
0677BA
7BADD7
CADEEF
E8F1F8
0094D4
00A9DD
6FCCEA
C7EBF8
E9F6FB
00AB8E
00BBA5
67D7C9
C6EFE9
E9F9F6

Requirements
Must have
• Double-sided
Nice to have
• Beach coastal theme
Should not have
• Any shape or drawing of of tooth or teeth. We don’t need these. You don't necessarily have to just cut and paste the logo art and text as a whole, you have the liberty to rearrange the text.

```html
<!DOCTYPE html>
<html lang="en">
<head>
<meta charset="utf-8">
<title>Brindle Oaks Orthodontics – Business Card</title>
<link rel="stylesheet" href="https://fonts.googleapis.com/css2?family=Raleway:wght@400;500;700&family=Varela+Round&display=swap">
<style>
  :root {
    --stage: #2e2e2e;
    --paper: #ffffff;
    --deep-teal: #3a8ca8;
    --soft-teal: #7fcdbd;
    --sea: #5cd8c8;
    --foam: #c9e8d3;
    --sand: #f7efd9;
    --ink: #2a2a2a;
    --muted: #555555;
    --rule: #c9c9c9;
    --pin: #d3182a;
  }
  * { box-sizing: border-box; margin: 0; padding: 0; }
  html, body { width: 1200px; height: 866px; overflow: hidden; }
  body {
    background: var(--stage);
    font-family: "Raleway", sans-serif;
    position: relative;
  }
  .card {
    position: absolute;
    top: 270px;
    width: 570px;
    height: 326px;
    background: var(--paper);
    overflow: hidden;
    box-shadow: 0 8px 24px rgba(0,0,0,.45);
  }
  .card--front { left: 20px; }
  .card--back { left: 610px; }

  /* Front */
  .contact { position: absolute; left: 42px; top: 34px; }
  .contact__name {
    font-family: "Varela Round", sans-serif;
    font-size: 26px; font-weight: 400; color: var(--deep-teal); letter-spacing: .5px;
  }
  .contact__role { font-size: 14px; color: var(--muted); margin: 2px 0 10px 4px; }
  .contact__line {
    display: flex; align-items: center; gap: 7px;
    font-size: 13px; color: var(--ink); margin: 3px 0 0 4px;
  }
  .contact__line svg { width: 13px; height: 13px; flex: none; }
  .practice {
    position: absolute; right: 34px; top: 148px;
    display: flex; align-items: center; gap: 10px;
  }
  .practice__dot { width: 30px; height: 30px; border-radius: 50%; background: var(--soft-teal); }
  .practice__name {
    font-family: "Varela Round", sans-serif;
    font-size: 22px; color: var(--deep-teal);
  }
  .address {
    position: absolute; right: 40px; top: 192px;
    text-align: right; font-size: 14px; line-height: 1.35; color: var(--ink);
  }
  .band {
    position: absolute; left: 0; width: 100%;
    color: #fff; font-size: 14px; font-weight: 500;
    display: flex; align-items: center; padding-left: 42px; letter-spacing: .2px;
  }
  .band--specialty { top: 244px; height: 40px; background: var(--deep-teal); border-bottom: 2px solid #fff; }
  .band--promise { top: 286px; height: 40px; background: var(--soft-teal); }

  /* Back */
  .back-art { position: absolute; inset: 0; }
  .office-map {
    position: absolute; left: 20px; top: 205px; width: 220px; height: 110px;
    background: var(--sea);
  }
  .appointment {
    position: absolute; right: 40px; top: 26px;
    font-size: 24px; font-weight: 400; color: var(--sea); letter-spacing: .5px;
  }
  .appointment__line { position: absolute; height: 1px; background: var(--rule); }
  .back-pin { position: absolute; left: 168px; top: 262px; }
  .back-name {
    position: absolute; left: 190px; top: 268px;
    font-family: "Varela Round", sans-serif; font-size: 14px; color: #fff;
  }
</style>
</head>
<body>

  <section class="card card--front" aria-label="Business card front">
    <div class="contact">
      <h1 class="contact__name">Daniel Marsh</h1>
      <p class="contact__role">Managing Director</p>
      <p class="contact__line">
        <svg viewBox="0 0 14 14" aria-hidden="true"><rect x="1" y="3" width="12" height="8" fill="#3a8ca8"/><path d="M1 3 L7 8 L13 3" stroke="#fff" stroke-width="1.2" fill="none"/></svg>
        office@brindleoaksortho.com
      </p>
      <p class="contact__line">
        <svg viewBox="0 0 14 14" aria-hidden="true"><circle cx="7" cy="7" r="6" fill="#3a8ca8"/><path d="M1 7 H13 M7 1 V13 M3 3.5 Q7 6 11 3.5 M3 10.5 Q7 8 11 10.5" stroke="#fff" stroke-width=".9" fill="none"/></svg>
        www.brindleoaksortho.com
      </p>
    </div>

    <div class="practice">
      <span class="practice__dot"></span>
      <span class="practice__name">Brindle Oaks Orthodontics</span>
    </div>

    <p class="address">123 Street Name<br>City, State Zip code</p>

    <p class="band band--specialty">Specialist in Orthodontic and Maxillofacial Orthopedics</p>
    <p class="band band--promise">Creating Tolvering smiles for Children and Adults</p>
  </section>

  <section class="card card--back" aria-label="Business card back">
    <svg class="back-art" viewBox="0 0 570 326" aria-hidden="true">
      <defs>
        <linearGradient id="sand" x1="0" y1="0" x2="1" y2="0">
          <stop offset="0" stop-color="#fbf5e3"/>
          <stop offset="1" stop-color="#f3e8c8"/>
        </linearGradient>
      </defs>
      <path d="M0 60 C120 50 220 110 330 130 C430 150 510 120 570 100 V326 H0 Z" fill="url(#sand)"/>
      <path d="M0 110 C110 90 210 150 320 170 C420 190 500 165 570 150 V326 H0 Z" fill="var(--foam)"/>
      <path d="M0 130 C110 110 210 175 320 195 C420 212 500 190 570 178 V326 H0 Z" fill="var(--sea)"/>
    </svg>

    <div class="office-map" role="img" aria-label="Map to the office"></div>

    <h2 class="appointment">Next Appointment</h2>
    <span class="appointment__line" style="right:40px;top:80px;width:230px;"></span>
    <span class="appointment__line" style="right:40px;top:110px;width:300px;"></span>

    <svg class="back-pin" width="16" height="22" viewBox="0 0 16 22" aria-hidden="true">
      <path d="M8 0 C3.5 0 0 3.5 0 8 C0 13 8 22 8 22 C8 22 16 13 16 8 C16 3.5 12.5 0 8 0 Z" fill="var(--pin)"/>
      <circle cx="8" cy="8" r="3" fill="#fff"/>
    </svg>
    <p class="back-name">Brindle Oaks Orthodontics</p>
  </section>

</body>
</html>
```